Coastline Premier Retreats Business Card Design

Design a business card for Coastline Premier Retreats. Look at the website for colors and reference. Card should have logo, name, title, office number, mobile number, email, URL and a tagline like, "Luxury Hotel & Resort Email Marketing" (This might change).

https://www.coastlinepremierretreats.example

The rest I will leave up to your imagination.

Contact Information for Business Card

Logo, name, title, office number, mobile number, email, URL and a tagline like, "Luxury Hotel & Resort Email Marketing" (This might change).

```html
<!DOCTYPE html>
<html lang="en">
<head>
<meta charset="utf-8">
<title>Coastline Premier Retreats – Business Card</title>
<link rel="stylesheet" href="https://fonts.googleapis.com/css2?family=Montserrat:wght@400;500;700;800&display=swap">
<style>
  :root {
    --bg: #1c1c1c;
    --card: #181818;
    --card-edge: #222222;
    --orange: #f07b14;
    --white: #f4f4f4;
    --emboss: #262626;
  }
  * { margin: 0; padding: 0; box-sizing: border-box; }
  html, body { width: 1200px; height: 915px; overflow: hidden; }
  body {
    background: var(--bg);
    font-family: "Montserrat", Arial, sans-serif;
    position: relative;
  }
  .card {
    position: absolute;
    width: 540px;
    height: 308px;
    background: var(--card);
    border: 1px solid var(--card-edge);
    box-shadow: 0 14px 30px rgba(0,0,0,0.55);
    overflow: hidden;
  }
  .card-front { left: 70px; top: 90px; }
  .card-back { left: 600px; top: 500px; }

  /* front */
  .front-name {
    position: absolute;
    left: 0; right: 0; top: 96px;
    text-align: center;
    font-weight: 800;
    font-size: 30px;
    letter-spacing: 1px;
    text-transform: uppercase;
    color: var(--emboss);
    line-height: 1.15;
  }
  .tagline {
    position: absolute;
    left: 0; right: 0; top: 214px;
    text-align: center;
    font-weight: 500;
    font-size: 17px;
    color: var(--orange);
  }

  /* back */
  .brand {
    position: absolute;
    left: 34px; top: 46px;
    display: flex;
    align-items: center;
    gap: 10px;
  }
  .brand-square { width: 14px; height: 14px; background: var(--orange); }
  .brand-name {
    font-weight: 700;
    font-size: 17px;
    color: var(--white);
    text-transform: uppercase;
    letter-spacing: 0.5px;
    line-height: 1.2;
  }
  .accent-bar {
    position: absolute;
    right: 0; top: 40px;
    width: 26px; height: 36px;
    background: var(--orange);
  }
  .person {
    position: absolute;
    right: 40px; top: 40px;
    text-align: right;
  }
  .person-name {
    font-weight: 700;
    font-size: 23px;
    color: var(--orange);
    text-transform: uppercase;
    letter-spacing: 0.5px;
  }
  .person-title {
    font-weight: 500;
    font-size: 12px;
    color: var(--white);
    margin-top: 2px;
  }
  .divider { position: absolute; left: 0; top: 0; }
  .contacts {
    position: absolute;
    left: 40px; top: 208px;
    list-style: none;
  }
  .contacts li {
    display: flex;
    align-items: center;
    gap: 9px;
    font-size: 14px;
    color: var(--white);
    margin-bottom: 7px;
  }
  .contacts .note { color: var(--orange); font-size: 11px; }
  .contacts svg { width: 13px; height: 13px; flex: none; }
</style>
</head>
<body>
  <section class="card card-front">
    <p class="front-name">Coastline<br>Premier Retreats</p>
    <p class="tagline">Luxury Hotel &amp; Resort Email Marketing</p>
  </section>

  <section class="card card-back">
    <div class="brand">
      <span class="brand-square"></span>
      <span class="brand-name">Coastline<br>Premier Retreats</span>
    </div>

    <div class="accent-bar"></div>
    <div class="person">
      <p class="person-name">Daniel Reeve</p>
      <p class="person-title">Managing Director</p>
    </div>

    <svg class="divider" width="540" height="308" viewBox="0 0 540 308" aria-hidden="true">
      <line x1="330" y1="95" x2="500" y2="95" stroke="#f4f4f4" stroke-width="1"/>
      <line x1="330" y1="95" x2="40" y2="196" stroke="#f07b14" stroke-width="1.2"/>
    </svg>

    <ul class="contacts">
      <li>
        <svg viewBox="0 0 14 14" aria-hidden="true"><rect x="3.5" y="1" width="7" height="12" rx="1.2" fill="none" stroke="#f07b14" stroke-width="1.4"/><circle cx="7" cy="11" r="0.8" fill="#f07b14"/></svg>
        <span>555.014.2870 <span class="note">(Mobile)</span></span>
      </li>
      <li>
        <svg viewBox="0 0 14 14" aria-hidden="true"><path d="M2 5 Q7 1 12 5 L11 7 L9 6 L9 5 Q7 4 5 5 L5 6 L3 7 Z" fill="#f07b14"/><rect x="3" y="8" width="8" height="4" rx="1" fill="#f07b14"/></svg>
        <span>555.014.6000 <span class="note">(Office)</span></span>
      </li>
      <li>
        <svg viewBox="0 0 14 14" aria-hidden="true"><rect x="1" y="3" width="12" height="8.5" rx="1" fill="#f07b14"/><path d="M1.5 3.5 L7 8 L12.5 3.5" fill="none" stroke="#181818" stroke-width="1.2"/></svg>
        <span>dreeve@coastlinepremierretreats.example</span>
      </li>
    </ul>
  </section>
</body>
</html>
```